Corwin Beacon Lighting - Commercial & Residential Landscape Lighting

Landscape Lighting Services & Design: Create a website for our landscape lighting company. We would like the design to be tailored around this description:
Illuminate with Confidence. Designed with Precision. Installed with Care.
Locally and veteran-owned, we take pride in transforming outdoor spaces through innovative lighting solutions tailored to your vision. From landscape and holiday lighting to permanent installations, our effortless process and expert design deliver breathtaking results and lasting curb appeal. Backed by a lifetime warranty and quarterly service options, our commitment to quality and customer satisfaction is unwavering. Try before you buy and experience your home in a whole new light with our complimentary demo kit — see the stunning effects before you decide.
- Also, add in this information as well; Outdoor Lighting not only beautifies spaces but also significantly enhances safety by illuminating your home or business. Beautifully lit entrances deter potential intruders, making your home a safer place for your loved ones. we also offer quarterly service plans to ensure lighting equipment continues to operate & illuminate effectively throughout the year. Also mention we provide free estimates and we are offering a 10% discount to military, veterans, and first responders.

Target Market(s)

Luxury market

Industry/Entity Type

Landscape Lighting - Residential & Commercial Lighting Services

Coding

Coded - Design and coding required

Number of Pages Required

2 page

Colors
00AB8E
00BBA5
67D7C9
C6EFE9
E9F9F6
59FF00
82FF00
B8FF75
E3FFCB
F4FFEA
FFC000
F8CF3A
FAE287
FDF2CF
FEFAEE

Requirements
Must have
• a lead generation button where people can submit their information for us to reach out to them and schedule their free estimate, homepage, about page, contact page, products and services page, user friendly, easy to navigate, and it also must be engaging and eye popping, as well as appealing to the luxury market. Please use colors; verdent green, dark green, ivory, and sunny yellow. Also, include an about page that references our story; Derek is retired Army and he opened a fitness studio in 2017 with his wife Jolene. He has installed low voltage lighting in every home he lived in and for his friends and family over the years and decided to open his own business because he is passionate about beautifying outdoor landscapes and highlighting a properties full potential, not only in the day but at night as well all while providing safety and security for his clients. Having a deep respect for nature and landscaping, he wants to provide the same care and quality to each of his clients as he has in the fitness industry for decades. He believes small businesses are the back bone of America and he's excited to provide a service that is all to often neglected in the design of a home.
Nice to have
• I would like to have a clear intent and purpose, engaging web design, clear call to action, optimized for search engines, mobile friendy design, security measures, credibility indicators

```html
<!DOCTYPE html>
<html lang="en">
<head>
<meta charset="utf-8">
<title>Corwin Beacon Lighting – Residential &amp; Commercial Landscape Lighting</title>
<link href="https://fonts.googleapis.com/css2?family=Poppins:wght@400;500;600;700;800&display=swap" rel="stylesheet">
<style>
:root{
  --yellow:#FBB62B;
  --yellow-deep:#FFC000;
  --green-dark:#176653;
  --green-mid:#1E9C7F;
  --teal-night:#0F4549;
  --ivory:#F6EBCB;
  --ink:#1E1E1E;
  --text:#3A3A3A;
  --brand-red:#C8202F;
  --navy:#1E2A8C;
  --white:#FFFFFF;
}
*{margin:0;padding:0;box-sizing:border-box}
html,body{width:1200px;height:3414px;overflow:hidden}
body{font-family:'Poppins',sans-serif;color:var(--text);background:var(--white);position:relative}
.abs{position:absolute}
.btn{position:absolute;display:flex;align-items:center;justify-content:center;background:var(--yellow);color:var(--white);font-weight:600;font-size:16px;letter-spacing:.3px;text-transform:uppercase;text-decoration:none}
.btn-outline{background:transparent;border:2px solid var(--white)}
.btn-framed{border:2px solid var(--white);outline:0}

/* header */
.site-header{position:absolute;left:0;top:0;width:1200px;height:127px;background:var(--white)}
.brand{position:absolute;left:74px;top:34px;display:flex;align-items:center;gap:10px}
.brand-dot{width:16px;height:16px;border-radius:50%;background:var(--yellow)}
.brand-name{font-weight:600;font-size:22px;line-height:1.1;color:var(--brand-red);width:200px}
.nav a{position:absolute;top:54px;font-size:15px;color:var(--ink);text-decoration:none}
.nav a.active{color:var(--brand-red);font-weight:600;border-bottom:2px solid var(--brand-red);padding-bottom:2px}

/* hero */
.hero{position:absolute;left:0;top:127px;width:1200px;height:593px;background:linear-gradient(110deg,#0f1714 0%,#26302a 35%,#7a5638 60%,#b98a55 72%,#3a4a2c 90%,#1b2418 100%)}
.hero-cut{position:absolute;left:0;top:670px;width:1200px;height:60px}
.hero h1{position:absolute;left:74px;top:306px;color:var(--white);font-weight:800;font-size:39px;line-height:43px;text-transform:uppercase}
.dots{position:absolute;top:628px;left:562px;display:flex;gap:12px}
.dots span{width:11px;height:11px;border-radius:50%;background:var(--white)}
.dots span:first-child{background:var(--green-mid)}

/* welcome */
.bar{position:absolute}
.photo{position:absolute}
h2.section-title{position:absolute;font-weight:500;font-size:34px;line-height:40px;color:var(--ink);text-transform:uppercase;letter-spacing:.5px}
.copy{position:absolute;font-size:15px;line-height:29.7px;color:var(--text)}

/* demo band */
.demo{position:absolute;left:0;top:1287px;width:1200px;height:348px;background:linear-gradient(180deg,#0d3b40 0%,#145c48 55%,#1d7a3a 100%);text-align:center}
.demo .lead{position:absolute;left:0;width:1200px;top:68px;color:var(--white);font-size:29px;line-height:39px;font-weight:500}
.demo .accent{position:absolute;left:0;width:1200px;top:157px;color:var(--yellow);font-weight:700;font-size:23px}

/* features */
.features-photo{position:absolute;left:0;top:2257px;width:496px;height:439px;background:linear-gradient(160deg,#1c2c3c 0%,#3c4a52 40%,#6a5036 60%,#243a20 100%)}
.features{position:absolute;left:496px;top:2257px;width:704px;height:439px;background:var(--green-dark)}
.feature{position:absolute;left:29px;width:602px;display:flex;align-items:center;color:var(--white);font-size:15px;line-height:27px}
.feature .icon{flex:0 0 78px;height:78px;border-radius:50%;background:rgba(255,255,255,.14);display:flex;align-items:center;justify-content:center;margin-right:20px}
.feature.is-active{background:var(--green-mid);height:102px;padding-left:14px}
.feature.is-active .icon{background:var(--yellow)}

/* discount */
.ivory-wedge{position:absolute;left:0;top:2880px;width:1200px;height:534px}
.offer{position:absolute;left:74px;top:2775px;width:1053px;height:252px;background:linear-gradient(90deg,#151515 0%,#2b2620 50%,#1a1814 100%)}
.offer p{position:absolute;left:52px;top:62px;color:var(--white);font-size:36px;line-height:43px;font-weight:500;text-transform:uppercase}
.offer p strong{color:var(--yellow);font-weight:700}

/* footer */
.footer-about{position:absolute;left:74px;top:3219px;width:350px;font-size:13px;line-height:24px;color:var(--ink)}
.footer-title{position:absolute;top:3092px;font-weight:700;font-size:16px;color:var(--navy)}
.footer-list{position:absolute;list-style:none;font-size:15px;color:var(--ink)}
.footer-list li{height:35.5px}
.social{position:absolute;left:721px;top:3276px;display:flex;gap:18px}
.social span{width:22px;height:22px;border-radius:50%;background:var(--ink)}
.rule{position:absolute;left:0;top:3352px;width:1200px;height:1px;background:#d9cba2}
.copyright{position:absolute;left:0;width:1200px;top:3376px;text-align:center;font-size:12px;color:var(--text)}
</style>
</head>
<body>

<header class="site-header">
  <div class="brand"><span class="brand-dot"></span><span class="brand-name">Corwin Beacon Lighting</span></div>
  <nav class="nav">
    <a href="#" class="active" style="left:418px">Home</a>
    <a href="#" style="left:505px">About Us</a>
    <a href="#" style="left:614px">Products &amp; Services</a>
    <a href="#" style="left:804px">Contact Us</a>
  </nav>
  <a href="#" class="btn" style="left:920px;top:37px;width:207px;height:53px">Get Free Estimates</a>
</header>

<section class="hero" role="img" aria-label="Brick home at dusk with warm landscape lighting on facade and garden"></section>
<svg class="hero-cut" viewBox="0 0 1200 60" preserveAspectRatio="none"><polygon points="0,50 200,10 1200,10 1200,60 0,60" fill="#fff"/></svg>
<h1 class="hero abs" style="all:unset;position:absolute;left:74px;top:306px;color:#fff;font-family:'Poppins',sans-serif;font-weight:800;font-size:39px;line-height:43px;text-transform:uppercase">Illuminate with confidence.<br>Designed with precision.<br>Installed with care</h1>
<a href="#" class="btn" style="left:76px;top:455px;width:206px;height:52px">Get Free Estimates</a>
<a href="#" class="btn btn-outline" style="left:297px;top:455px;width:135px;height:52px">Read More</a>
<div class="dots"><span></span><span></span><span></span><span></span></div>

<div class="bar" style="left:60px;top:994px;width:14px;height:179px;background:var(--yellow)"></div>
<div class="bar" style="left:587px;top:838px;width:13px;height:310px;background:var(--green-dark)"></div>
<div class="photo" role="img" aria-label="Modern two-storey house lit at twilight with garden path lights" style="left:74px;top:798px;width:513px;height:391px;background:linear-gradient(160deg,#1d3fa0 0%,#2a56c0 40%,#c9a070 65%,#2f6a2a 100%)"></div>
<h2 class="section-title" style="left:636px;top:804px">Welcome to<br>Corwin Beacon Lighting</h2>
<p class="copy" style="left:636px;top:895px;width:492px">Locally and veteran-owned, we take pride in transforming outdoor spaces through innovative lighting solutions tailored to your vision. From landscape and holiday lighting to permanent installations, our effortless process and expert design deliver breathtaking results and lasting curb appeal. Backed by a lifetime warranty and quarterly service options, our commitment to quality and customer satisfaction is unwavering.</p>
<a href="#" class="btn" style="left:636px;top:1124px;width:157px;height:53px">Read More</a>

<section class="demo" role="img" aria-label="Modern home exterior glowing with green accent lighting">
  <p class="lead">Try before you buy and experience your home in a whole<br>new light with our complimentary demo kit.</p>
  <p class="accent">SEE THE STUNNING EFFECTS BEFORE YOU DECIDE.</p>
</section>
<a href="#" class="btn" style="left:521px;top:1508px;width:158px;height:51px">Try Demo Kit</a>

<h2 class="section-title" style="left:74px;top:1730px">Story about Derek</h2>
<p class="copy" style="left:74px;top:1779px;width:606px">Derek is retired Army and he opened a fitness studio in 2017 with his wife Jolene. He has installed low voltage lighting in every home he lived in and for his friends and family over the years and decided to open his own business because he is passionate about beautifying outdoor landscapes and highlighting a properties full potential, not only in the day but at night as well all while providing safety and security for his clients. Having a deep respect for nature and landscaping, he wants to provide the same care and quality to each of his clients as he has in the fitness industry for decades. He believes small businesses are the back bone of America and he's excited to provide a service that is all to often neglected in the design of a home.</p>
<a href="#" class="btn" style="left:74px;top:2096px;width:158px;height:52px">Read More</a>
<div class="bar" style="left:690px;top:1732px;width:14px;height:181px;background:var(--yellow)"></div>
<div class="bar" style="left:1127px;top:1836px;width:13px;height:312px;background:var(--green-dark)"></div>
<div class="photo" role="img" aria-label="Portrait of the company founder in a denim shirt" style="left:704px;top:1711px;width:423px;height:465px;background:linear-gradient(180deg,#9fcfe2 0%,#8cc3da 55%,#3a6fa8 100%)"></div>

<div class="features-photo" role="img" aria-label="Home entrance and walkway illuminated at night"></div>
<section class="features">
  <div class="feature" style="top:71px">
    <span class="icon"><svg width="30" height="34" viewBox="0 0 30 34" fill="none" stroke="#fff" stroke-width="2.4"><path d="M15 3a10 10 0 0 0-6 18v4h12v-4a10 10 0 0 0-6-18z"/><path d="M10 29h10M12 33h6"/></svg></span>
    <span>Outdoor Lighting not only beautifies spaces but also significantly enhances safety by illuminating your home or business.</span>
  </div>
  <div class="feature is-active" style="top:164px">
    <span class="icon"><svg width="36" height="32" viewBox="0 0 36 32" fill="#fff"><path d="M18 2 2 16h5v14h8v-9h6v9h8V16h5z"/></svg></span>
    <span>Beautifully lit entrances deter potential intruders, making your home a safer place for your loved ones.</span>
  </div>
  <div class="feature" style="top:290px">
    <span class="icon"><svg width="30" height="32" viewBox="0 0 30 32" fill="none" stroke="#fff" stroke-width="2.4"><rect x="3" y="5" width="24" height="24" rx="2"/><path d="M3 12h24M9 2v6M21 2v6"/><path d="M9 17h3M14 17h3M19 17h3M9 23h3M14 23h3M19 23h3"/></svg></span>
    <span>We also offer quarterly service plans to ensure lighting equipment continues to operate &amp; illuminate effectively throughout the year.</span>
  </div>
</section>

<svg class="ivory-wedge" viewBox="0 0 1200 534" preserveAspectRatio="none" style="top:2880px"><polygon points="0,30 1200,0 1200,534 0,534" fill="#F6EBCB"/></svg>
<section class="offer" role="img" aria-label="Lit home at night behind a dark overlay">
  <p>We are offering a<br><strong>10% discount</strong> to military, veterans,<br>and first responders.</p>
</section>
<a href="#" class="btn btn-framed" style="left:871px;top:2876px;width:204px;height:51px">Get Free Estimates</a>

<div class="brand" style="top:3110px"><span class="brand-dot"></span><span class="brand-name">Corwin Beacon Lighting</span></div>
<p class="footer-about">Locally and veteran-owned, we take pride in transforming outdoor spaces through innovative lighting solutions tailored to your vision.</p>
<h3 class="footer-title" style="left:443px">QUICK LINKS</h3>
<ul class="footer-list" style="left:443px;top:3127px"><li>Home</li><li>About Us</li><li>Products &amp; Services</li><li>Contact Us</li></ul>
<h3 class="footer-title" style="left:721px">CONTACT INFO</h3>
<ul class="footer-list" style="left:721px;top:3127px;line-height:28px">
  <li style="height:auto">48 Lantern Row Suite 12,<br>Fairview 20451, United States</li>
  <li style="height:auto;margin-top:8px">+1 555-014-2290</li>
  <li style="height:auto;margin-top:8px">info@corwinbeacon.com</li>
</ul>
<div class="social"><span></span><span></span><span></span><span></span><span></span></div>
<div class="rule"></div>
<p class="copyright">Copyright © 2025. Corwin Beacon Lighting. All Right Reserved</p>

</body>
</html>
```